Morvane Capital, a private equity fund, needs a brochure

Morvane Capital is a private equity fund dedicated to the development of budget hotels in France (reasonably priced hotel rooms).
Our customers are French private and high-income investors.

The brochure should communicate :
- seriousness and expertise
- trust, confidence and security
- financial product and profitability

The title is : Investissez dans l'hôtellerie économique et l'immobilier

Brochure size :
3 pages A4
Open size : 63 x 29,7 cm
Closed size : 21 x 29,7 cm

Our competitors :
Trelisse http://trelisse-immo-horizon.example/
789 Parcours http://www.789parcours.example/
GLD Capital http://www.gldam.example/
Soltane capital http://www.soltanecapital.example/
Barostel http://www.barostel.example/

Target Market(s)

Private investors, high-income ; Institutional investors ; Target customers are French private investors with high revenue.

Industry/Entity Type

Financial

Requirements
Must have
• - Brochure must respect our identity (you can see our logo) and use its colors and typo (and/or same typo style)
- You must use pictures on each interior pages (pictures of projetc and hotels)

```html
<!DOCTYPE html>
<html lang="fr">
<head>
<meta charset="utf-8">
<title>Morvane Capital – Quatrième de couverture</title>
<link href="https://fonts.googleapis.com/css2?family=Arimo:wght@400;700&family=Libre+Caslon+Text:wght@700&family=Roboto+Condensed:wght@700&display=swap" rel="stylesheet">
<style>
  :root{
    --backdrop:#3a4248;
    --page:#dde1e3;
    --band:#e8eae6;
    --ink:#1e1e1e;
    --muted:#3a3a3a;
    --red:#c8202f;
    --rule:#6d6d6d;
    --frame:#8a8a8a;
  }
  *{margin:0;padding:0;box-sizing:border-box}
  html,body{width:900px;height:1200px;overflow:hidden;background:var(--backdrop)}
  body{position:relative;font-family:"Arimo",Arial,sans-serif;color:var(--ink)}
  .page{position:absolute;left:61px;top:46px;width:775px;height:1106px;background:var(--page);overflow:hidden}
  .photo-band{position:absolute;left:35px;top:111px;width:740px;height:220px;background:var(--band)}
  .photo{position:absolute;top:15px;height:188px}
  .photo--reception{left:14px;width:239px;background:linear-gradient(160deg,#e9e4df 0%,#b4473f 45%,#7a4b34 75%,#d8d2cc 100%)}
  .photo--facade{left:268px;width:239px;background:linear-gradient(180deg,#3d7fc4 0%,#b9cfe2 35%,#a8734d 60%,#4b4a4a 100%)}
  .photo--balcony{left:521px;width:219px;background:linear-gradient(135deg,#f0c27a 0%,#a7683a 45%,#3b2418 100%)}
  .notice{position:absolute;left:35px;top:372px;width:506px;height:264px;border:1px solid var(--frame);padding:11px 12px 0 13px;font-size:9.4px;line-height:15.7px;color:var(--muted)}
  .notice p{margin-bottom:15.7px}
  .notice strong{color:var(--ink);font-weight:700}
  .notice .bullet{display:inline-block;width:7px;height:7px;background:var(--red);margin-right:9px;vertical-align:0}
  .brand{position:absolute;left:0;right:-14px;top:835px;text-align:center}
  .brand-name{display:inline-flex;align-items:center;gap:10px;font-family:"Libre Caslon Text",Georgia,serif;font-variant:small-caps;font-size:29px;font-weight:700;color:var(--ink);letter-spacing:.6px;line-height:34px}
  .brand-name .mark{width:12px;height:12px;background:var(--red)}
  .address{position:absolute;left:0;right:-14px;top:876px;text-align:center;font-size:12.2px;font-weight:700;line-height:18px}
  .rule{position:absolute;left:141px;width:510px;height:1px;background:var(--rule)}
  .rule--top{top:924px}
  .rule--bottom{top:1004px}
  .contact{position:absolute;top:929px;font-size:12.2px;line-height:15.6px}
  .contact--left{left:147px}
  .contact--right{left:516px}
  .contact h3{font-family:"Roboto Condensed","Arial Narrow",sans-serif;color:var(--red);font-size:14px;font-weight:700;line-height:18px}
  .contact .name{font-weight:700}
  .legal{position:absolute;left:0;right:-14px;top:1011px;text-align:center;font-size:10.2px;line-height:15.5px;color:var(--muted)}
  .portrait{position:absolute}
  .portrait--left{left:0;top:904px;width:138px;height:202px;background:linear-gradient(180deg,#b9b5ae 0%,#8a7467 35%,#2b2d33 65%,#1c1d22 100%)}
  .portrait--right{left:660px;top:899px;width:115px;height:207px;background:linear-gradient(180deg,#c8c4bd 0%,#9a7c6a 35%,#2a2c32 65%,#1a1b20 100%)}
</style>
</head>
<body>
  <main class="page">
    <section class="photo-band">
      <div class="photo photo--reception" role="img" aria-label="Photo de la réception d'un hôtel économique"></div>
      <div class="photo photo--facade" role="img" aria-label="Photo de la façade d'un hôtel avec terrasse de restaurant"></div>
      <div class="photo photo--balcony" role="img" aria-label="Photo d'une enseigne Hotel sur un balcon parisien"></div>
    </section>

    <section class="notice">
      <p><span class="bullet"></span><strong>Avertissement important:</strong> la présente notice d'information relative à la souscription à l'augmentation de capital de Morvane Capital, SAS à capital variable, ne constitue pas une offre au public de titres financiers au sens de l'article L. 411-1 du Code monétaire et financier (CMF). L'investissement dans Morvane Capital est réservé aux investisseurs qui effectuent une souscription minimale de 100.000 euros conformément aux dispositions du paragraphe 2° du I de l'article L. 422-2 du CMF. L'opération présentée ne donne donc pas lieu à un prospectus soumis au visa de l'Autorité des Marchés Financiers.</p>
      <p>Les personnes ou entités mentionnées au 2° du II de l'article L. 411-2 du CMF ne peuvent participer à cette offre que pour compte propre dans les conditions fixées par les articles D. 411-1, D. 411-2, D. 734-1, D. 744-1, D. 754-1 et D. 764-1 du CMF.</p>
      <p>La diffusion, directe ou indirecte, dans le public des instruments financiers ainsi acquis ne peut être réalisée que dans les conditions prévues aux articles L. 411-1, L. 411-2, L. 412-1 et L. 621-8 à L. 621-8-3 du CMF.</p>
    </section>

    <div class="brand"><span class="brand-name"><span class="mark"></span>Morvane Capital</span></div>
    <div class="address">42 rue des Lisières 75017 &nbsp;–&nbsp; Paris<br>Téléphone: 01 40 27 63 18 &nbsp;–&nbsp; Fax: 01 40 27 63 19</div>

    <div class="rule rule--top"></div>
    <div class="contact contact--left">
      <h3>Investisseurs institutionnels</h3>
      <div class="name">Étienne-Marc Valdoré</div>
      <div>06 12 48 30 77</div>
      <div>emv@groupelv.example</div>
    </div>
    <div class="contact contact--right">
      <h3>Relations partenaires</h3>
      <div class="name">Arnaud de Brévilly</div>
      <div>06 35 90 14 82</div>
      <div>adb@groupelv.example</div>
    </div>
    <div class="rule rule--bottom"></div>

    <div class="legal">Morvane Capital, société par actions simplifiée à capital variable<br>Siège social: Immeuble CALVERA, 12 zone de Pérelle, 97232 Le Lamentin<br>812 456 903 RCS Fort de France</div>

    <div class="portrait portrait--left" role="img" aria-label="Portrait du responsable investisseurs institutionnels"></div>
    <div class="portrait portrait--right" role="img" aria-label="Portrait du responsable relations partenaires"></div>
  </main>
</body>
</html>
```